Advertising company unique advertising platform

we need a logo design for a new company based in Australia Melbourne. We develop innovated advertising platform where consumer can use this platform to get regular discount, as business owner they can use this platform for free advertisement. Payment for this advertisement platform only payable every two weeks, when I generate revenue for their business

Industry/Entity Type

Advertising

Contact Information for Business Card

Dale Morven | Co-Founder |Managing Director
Suite 718 240 Wattlebrook Lane Melbourne Vic 3000

ABN 38 614 207 923
Tel: +61 0487 259 318 | Email: dale.morven@plivorantu.com

Font styles to use
Decorative
Script

Requirements
Must have
• Try few different design and some round corner business card
Should not have
• One round corner business card...try 4 different colour background not only black, make sure two side is designed. Be creative so imagine you are giving this to a client make sure has wow factor, if you can also try one design with engrave like all the logo, words look 3d feel
• The word Advertising Platform use attached file font

```html
<!DOCTYPE html>
<html lang="en">
<head>
<meta charset="utf-8">
<title>Plivorantu Business Card</title>
<link rel="stylesheet" href="https://fonts.googleapis.com/css2?family=Source+Sans+3:wght@400;600;700&display=swap">
<style>
  :root {
    --backdrop: #35302d;
    --card: #1a1a1c;
    --flame: #f0623a;
    --teal: #2fd3b0;
    --ink: #f1f1f1;
    --muted: #9a9a9a;
  }
  html, body {
    margin: 0;
    padding: 0;
    width: 1200px;
    height: 864px;
    overflow: hidden;
    background: var(--backdrop);
    font-family: "Source Sans 3", sans-serif;
  }
  .stage {
    position: relative;
    width: 1200px;
    height: 864px;
    display: flex;
    align-items: center;
    justify-content: center;
    gap: 40px;
  }
  .card {
    position: relative;
    width: 520px;
    height: 297px;
    background: var(--card);
    border-radius: 6px;
    box-shadow: 0 10px 30px rgba(0,0,0,0.45);
    overflow: hidden;
  }
  /* Front */
  .card-front .brand {
    position: absolute;
    left: 118px;
    top: 96px;
    display: flex;
    align-items: center;
    gap: 14px;
  }
  .brand-dot {
    width: 40px;
    height: 40px;
    border-radius: 50%;
    background: var(--flame);
  }
  .brand-name {
    font-size: 38px;
    font-weight: 700;
    color: var(--flame);
    letter-spacing: 0.5px;
  }
  .card-front .website {
    position: absolute;
    left: 96px;
    top: 212px;
    font-size: 13px;
    letter-spacing: 4px;
    color: var(--muted);
  }
  /* Back */
  .card-back .brand {
    position: absolute;
    left: 34px;
    top: 126px;
    display: flex;
    align-items: center;
    gap: 8px;
  }
  .card-back .brand-dot {
    width: 22px;
    height: 22px;
  }
  .card-back .brand-name {
    font-size: 22px;
  }
  .divider {
    position: absolute;
    left: 196px;
    top: 36px;
    width: 2px;
    height: 200px;
    background: linear-gradient(to bottom, rgba(200,200,200,0.85), rgba(200,200,200,0));
  }
  .details {
    position: absolute;
    left: 214px;
    top: 34px;
    line-height: 22px;
    font-size: 16px;
    color: var(--ink);
  }
  .details p { margin: 0; }
  .person-name {
    color: var(--flame);
    font-weight: 700;
    text-transform: uppercase;
  }
  .person-role {
    color: var(--teal);
    font-weight: 600;
    text-transform: uppercase;
    font-size: 17px;
  }
  .company { margin-top: 4px !important; }
  .contact-line {
    display: flex;
    align-items: center;
    gap: 8px;
  }
  .contact-line svg { flex: none; }
</style>
</head>
<body>
<main class="stage">
  <section class="card card-front" aria-label="Card front">
    <div class="brand">
      <span class="brand-dot"></span>
      <span class="brand-name">Plivora Hub</span>
    </div>
    <p class="website">www.plivorantu.com</p>
  </section>

  <section class="card card-back" aria-label="Card back">
    <div class="brand">
      <span class="brand-dot"></span>
      <span class="brand-name">Plivora Hub</span>
    </div>
    <div class="divider"></div>
    <div class="details">
      <p class="person-name">Dale Morven</p>
      <p class="person-role">Co-Founder</p>
      <p class="person-role">Managing Director</p>
      <p class="company">Plivorantu</p>
      <p>ABN 38 614 207 923</p>
      <p>Suite 718 240 Wattlebrook Lane</p>
      <p>Melbourne Vic 3000</p>
      <p class="contact-line">
        <svg width="12" height="12" viewBox="0 0 12 12" aria-hidden="true">
          <path d="M2 1h2.5l1 2.5-1.3 1a6 6 0 0 0 3.3 3.3l1-1.3L11 7.5V10a1 1 0 0 1-1 1A9 9 0 0 1 1 2a1 1 0 0 1 1-1z" fill="var(--flame)"/>
        </svg>
        +61 0487 259 318
      </p>
      <p class="contact-line">
        <svg width="12" height="10" viewBox="0 0 12 10" aria-hidden="true">
          <rect x="0" y="0" width="12" height="10" rx="1" fill="var(--flame)"/>
          <path d="M0.5 1 6 5.5 11.5 1" fill="none" stroke="var(--card)" stroke-width="1.2"/>
        </svg>
        dale.morven@plivorantu.com
      </p>
    </div>
  </section>
</main>
</body>
</html>
```